Maison Belvert Tees

Our mission is simple...to provide cozy, comfy cotton separates that mix and match for endless wardrobe possibilities! Everything is easy care, easy wear and perfect for cruising, vacations on sandy beaches or travel to chilly weather climates year round! From footwear (ORV, Tevlo, Paridu) to swimwear (Quilta, Marovee, Zobu) and stylish fashion from top designers (Castelmo, Breezy Ateliers, Bright Harvest, Dunmore Garment Co., Pia Bloom, Kelo Brant, Finchetta) just to name a few.Don't forget the finishing touches...we carry beautiful scarves, unique jewelry and a variety of hats for every occasion.The best selection of imprinted T-Shirts and Sweatshirts in the Napa Valley

Target Market(s)

Mostly women, but clothing, swimwear and footwear for the whole family. We have sizing from infant to 2x

Requirements
Must have
• swimwear as one of the main features, All the clothing line logos, address and phone # of store
• Front of card showing more the boutique side of store, back of card everything else
• description of store
Nice to have
• We are 2/3 boutique and a 1/3 imprinted T-shirts and sweat shirts for Calistoga and Napa Valley...Largest selection in the valley
• We carry a complete line of the best sunscreen product available~Rayglo
• Huge selection of Kelo Brant sunglasses
• In business for over 29 years

```html
<!DOCTYPE html>
<html lang="en">
<head>
<meta charset="utf-8">
<title>Maison Belvert Tees – Rack Card</title>
<link rel="stylesheet" href="https://fonts.googleapis.com/css2?family=Short+Stack&family=Anonymous+Pro&family=PT+Sans:ital,wght@0,400;0,700;1,400;1,700&display=swap">
<style>
  :root {
    --page: #ebe8e4;
    --leaf: #a7d08c;
    --leaf-ring: #e2f1d6;
    --band: #a4a4a4;
    --white: #ffffff;
    --logo-ink: #3a3a3a;
  }
  * { margin: 0; padding: 0; box-sizing: border-box; }
  html, body { width: 1200px; height: 1128px; overflow: hidden; }
  body { background: var(--page); position: relative; }

  .rack-card {
    position: absolute; top: 94px; width: 429px; height: 933px;
    background: var(--leaf); overflow: hidden;
    box-shadow: 0 4px 10px rgba(0,0,0,.18);
  }
  .rack-card--front { left: 97px; }
  .rack-card--back { left: 675px; }
  .card-art { position: absolute; inset: 0; width: 429px; height: 933px; }

  .brand-title {
    position: absolute; left: 0; width: 100%; text-align: center;
    font-family: "Short Stack", cursive; color: var(--white);
    letter-spacing: 4px; line-height: 1.2; font-weight: 400;
  }
  .brand-tagline {
    position: absolute; left: 0; width: 100%; text-align: center;
    font-family: "PT Sans", sans-serif; color: var(--white); letter-spacing: 1.5px;
  }
  .rack-card--front .brand-title { top: 16px; font-size: 33px; }
  .rack-card--front .brand-tagline { top: 114px; font-size: 11px; }

  .store-copy {
    position: absolute; text-align: center; color: var(--white);
    font-family: "Anonymous Pro", monospace; white-space: nowrap;
  }
  .rack-card--front .store-copy { left: 0; width: 429px; top: 638px; font-size: 15px; line-height: 19.6px; }
  .store-copy p + p { margin-top: 20px; }

  .info-band {
    position: absolute; left: 0; width: 100%; background: var(--band);
    border-top: 4px solid var(--white); color: var(--white);
    font-family: "PT Sans", sans-serif; text-align: center;
    display: flex; flex-direction: column; justify-content: center;
  }
  .rack-card--front .info-band { top: 812px; height: 58px; font-size: 22px; }
  .rack-card--back .info-band { top: 784px; height: 86px; font-size: 17.5px; font-weight: 700; line-height: 26px; }

  .brand-strip {
    position: absolute; left: 0; top: 870px; width: 100%; height: 63px;
    background: var(--white); display: flex; align-items: center;
    justify-content: space-around; padding: 0 6px;
  }
  .brand-name {
    font-family: "PT Sans", sans-serif; font-weight: 700; color: var(--logo-ink);
    font-size: 15px; display: flex; align-items: center; gap: 4px; white-space: nowrap;
  }
  .brand-name--large { font-size: 19px; }
  .brand-mark { width: 10px; height: 10px; background: var(--logo-ink); display: inline-block; }
  .partner-badge { width: 46px; height: 46px; background: var(--band); }

  .rack-card--back .brand-title { top: 440px; left: 14px; width: 234px; font-size: 21px; letter-spacing: 2.5px; }
  .rack-card--back .brand-tagline { top: 504px; left: 14px; width: 234px; font-size: 9px; }
  .testimonial {
    position: absolute; left: 14px; width: 234px; top: 558px; text-align: center;
    font-family: "PT Sans", sans-serif; font-style: italic; color: var(--white);
    font-size: 11px; line-height: 15px; letter-spacing: -0.3px; white-space: nowrap;
  }
  .testimonial cite { font-style: italic; font-weight: 700; }
  .rack-card--back .store-copy { left: 14px; width: 234px; top: 664px; font-size: 12.5px; line-height: 19.6px; }
</style>
</head>
<body>

<section class="rack-card rack-card--front">
  <svg class="card-art" viewBox="0 0 429 933">
    <defs>
      <linearGradient id="heroTone" x1="0" y1="0" x2="1" y2="1">
        <stop offset="0" stop-color="#8f9d72"/>
        <stop offset="0.45" stop-color="#b08a67"/>
        <stop offset="1" stop-color="#e6c9ad"/>
      </linearGradient>
    </defs>
    <path fill="var(--white)" d="M0,270 C90,186 220,132 429,128 L429,146 C220,150 90,200 0,286 Z"/>
    <path role="img" aria-label="Smiling woman in a wide straw sun hat with a braid, wearing a white crochet top" fill="url(#heroTone)" d="M0,286 C90,200 220,150 429,146 L429,440 C330,540 200,590 0,594 Z"/>
    <path fill="var(--white)" d="M0,594 C200,590 330,540 429,440 L429,460 C330,568 200,612 0,614 Z"/>
  </svg>

  <h1 class="brand-title">MAISON BELVERT<br>TEES</h1>
  <p class="brand-tagline">resort and swimwear</p>

  <div class="store-copy">
    <p>Our mission is simple...to provide cozy,<br>comfy cotton separates that mix and match<br>for endless wardrobe possibilities!</p>
    <p>Everything is easy care, easy wear and perfect<br>for cruising, vacations on sandy beaches or<br>travel to chilly weather climates year round!</p>
  </div>

  <div class="info-band">www.maisonbelverttees.com</div>

  <div class="brand-strip">
    <span class="brand-name">Quilta</span>
    <span class="brand-name brand-name--large">Castelmo</span>
    <span class="brand-name">Bright Harvest</span>
    <span class="brand-name">Kelo Brant</span>
  </div>
</section>

<section class="rack-card rack-card--back">
  <svg class="card-art" viewBox="0 0 429 933">
    <defs>
      <linearGradient id="stairsTone" x1="0" y1="0" x2="1" y2="1">
        <stop offset="0" stop-color="#56653f"/>
        <stop offset="0.5" stop-color="#6e5b46"/>
        <stop offset="1" stop-color="#3f4a32"/>
      </linearGradient>
      <linearGradient id="sandalTone" x1="0" y1="0" x2="1" y2="1">
        <stop offset="0" stop-color="#a6d0e0"/>
        <stop offset="1" stop-color="#6fa9c4"/>
      </linearGradient>
      <radialGradient id="necklaceTone">
        <stop offset="0" stop-color="#fbf8f1"/>
        <stop offset="1" stop-color="#e9e3d6"/>
      </radialGradient>
    </defs>
    <path role="img" aria-label="Two women laughing while sitting on wooden garden steps" fill="url(#stairsTone)" d="M0,0 L429,0 L429,250 C340,340 200,380 0,390 Z"/>
    <path fill="var(--white)" d="M0,390 C200,380 340,340 429,250 L429,268 C340,360 200,404 0,410 Z"/>

    <g role="img" aria-label="Periwinkle lace scarf">
      <circle cx="337" cy="346" r="84" fill="var(--leaf-ring)"/>
      <circle cx="337" cy="346" r="76" fill="#7e88d4"/>
    </g>
    <g role="img" aria-label="Black flip-flop sandals with colorful straps">
      <circle cx="338" cy="518" r="84" fill="var(--leaf-ring)"/>
      <circle cx="338" cy="518" r="76" fill="url(#sandalTone)"/>
    </g>
    <g role="img" aria-label="Gold chain necklace">
      <circle cx="338" cy="694" r="84" fill="var(--leaf-ring)"/>
      <circle cx="338" cy="694" r="76" fill="url(#necklaceTone)"/>
    </g>
  </svg>

  <h2 class="brand-title">MAISON BELVERT<br>TEES</h2>
  <p class="brand-tagline">resort and swimwear</p>

  <blockquote class="testimonial">"So much fun in this store, bright and colorful..<br>I always find something cotton and MADE IN<br>THE USA". Lots of beautiful dresses, fun<br>bathing suits ( I forgot mine ) and friendly<br>knowledgable staff.- <cite>-Mira T. Oakdale, Ca.</cite></blockquote>

  <div class="store-copy">
    <p>At Maison Belvert Tees<br>you will find a fabulous,<br>fashionable selection of<br>clothing and accessories<br>for every taste and any budget.</p>
  </div>

  <div class="info-band">
    <span>2210 Orchard Ave. Valemont, Ca., 94870</span>
    <span>707-555-0183</span>
  </div>

  <div class="brand-strip">
    <span class="brand-name brand-name--large">Paridu</span>
    <span class="brand-name"><i class="brand-mark"></i>Tevlo</span>
    <span class="brand-name">Pia Bloom</span>
    <span class="partner-badge" role="img" aria-label="Partner badge"></span>
    <span class="brand-name brand-name--large">ORV</span>
  </div>
</section>

</body>
</html>
```